Website Design for Hulls for Heroes

Please design and code a new website.
Here are the sites I like best:
http://www.sailbrisk.com/alternate/
http://www.wheelsforhonor.org
Please make it similar. This is NOT a car donation site. It's a boat donation site. I just like this sites above as a lead generation sites.
Old site:
http://hullsforheroes.org
Updates
Coding
Coded - Design and coding required
Number of Pages Required
1 page
Look and feel
Each slider illustrates characteristics of the customer's brand and the style your logo design should communicate.

```html
<!DOCTYPE html>
<html lang="en">
<head>
<meta charset="utf-8">
<title>Hulls for Heroes – Donate Your Boat</title>
<link href="https://fonts.googleapis.com/css2?family=Oswald:wght@400;500;600;700&family=Open+Sans:wght@400;600;700&display=swap" rel="stylesheet">
<style>
:root{
  --navy:#13235a;
  --navy-deep:#0c1840;
  --blue:#1f3f96;
  --red:#c8202b;
  --red-dark:#a0161f;
  --white:#ffffff;
  --ink:#2b2f3a;
  --muted:#6a7080;
  --line:#d9dce4;
  --pale:#f3f4f8;
}
*{box-sizing:border-box;margin:0;padding:0}
html,body{width:1200px;height:2952px;overflow:hidden}
body{font-family:"Open Sans",Arial,sans-serif;color:var(--ink);background:var(--white)}
.head{font-family:"Oswald","Arial Narrow",sans-serif}

/* header */
.site-header{height:160px;background:linear-gradient(90deg,var(--navy-deep),var(--navy) 60%,var(--navy-deep));display:flex;align-items:center;justify-content:space-between;padding:0 60px}
.brand{display:flex;align-items:center;gap:16px;color:var(--white);font-family:"Oswald",sans-serif;font-size:46px;font-weight:600;letter-spacing:1px;text-transform:uppercase}
.brand .dot{width:26px;height:26px;border-radius:50%;background:var(--red)}
.call{display:flex;align-items:center;gap:16px;color:var(--white)}
.call .ring{width:64px;height:64px;border:3px solid var(--white);border-radius:50%;display:flex;align-items:center;justify-content:center}
.call small{display:block;font-family:"Oswald",sans-serif;font-size:20px;letter-spacing:1px}
.call strong{display:block;font-family:"Oswald",sans-serif;font-size:44px;line-height:1}
.call em{display:block;font-style:normal;font-size:13px;color:#c9d0e6}

/* nav */
.nav{height:48px;background:var(--red);display:flex;align-items:center;padding-left:170px;position:relative}
.nav a{color:var(--white);text-decoration:none;font-family:"Oswald",sans-serif;font-size:16px;margin-right:56px;letter-spacing:.5px}
.nav .tab{position:absolute;right:0;top:0;width:400px;height:48px;background:var(--navy);color:var(--white);font-family:"Oswald",sans-serif;font-size:22px;display:flex;align-items:center;justify-content:center;letter-spacing:.5px}

/* hero */
.hero{height:432px;position:relative;display:flex}
.hero-photo{flex:1;background:linear-gradient(100deg,#5b6a55 0%,#9aa6a8 35%,#d9e2ea 60%,#eef2f6 100%)}
.donate-form{width:400px;background:var(--white);padding:22px 28px;border-left:1px solid var(--line)}
.donate-form h3{font-size:17px;text-align:center;color:var(--navy);margin-bottom:14px;font-weight:700}
.row{display:flex;gap:10px;margin-bottom:10px}
.field{flex:1;height:34px;border:1px solid #b9bfcc;font-size:13px;color:var(--muted);padding:7px 10px}
.btn{display:block;margin:16px auto 0;width:150px;height:40px;background:var(--red);color:var(--white);border:0;font-family:"Oswald",sans-serif;font-size:18px}

/* banner */
.banner{height:300px;display:flex;background:var(--blue);margin-top:20px}
.banner-text{width:600px;background:linear-gradient(90deg,var(--navy) 0%,var(--blue) 100%);display:flex;flex-direction:column;justify-content:center;padding-left:100px;color:var(--white);text-transform:uppercase}
.banner-text .l1{font-size:36px;font-weight:500}
.banner-text .l2{font-size:92px;font-weight:700;color:var(--red);line-height:1;background:var(--white);padding:0 14px;width:max-content;margin:6px 0}
.banner-text .l3{font-size:44px;font-weight:600}
.perks{flex:1;display:flex;justify-content:space-around;align-items:center;padding:0 40px}
.perk{text-align:center;color:var(--white);width:110px}
.perk .ic{width:72px;height:72px;border:3px solid var(--white);border-radius:50%;margin:0 auto 12px;display:flex;align-items:center;justify-content:center}
.perk p{font-size:13px;line-height:1.3}

/* how */
.how{height:320px;padding-top:40px;text-align:center}
.section-title{font-family:"Oswald",sans-serif;font-size:40px;font-weight:600;color:var(--navy);text-transform:uppercase}
.section-title span{color:var(--red)}
.rule{width:70px;height:4px;background:var(--red);margin:10px auto 36px}
.steps{display:flex;justify-content:center;gap:70px}
.step{width:300px;text-align:left;display:flex;gap:16px}
.step .ic{flex:none;width:56px}
.step h4{font-family:"Oswald",sans-serif;font-size:19px;color:var(--red);line-height:1.2;margin-bottom:10px}
.step p{font-size:13px;color:var(--muted);line-height:1.5}

/* why */
.why{height:720px;background:linear-gradient(180deg,#0e1c4f,#1a2f78);position:relative;color:var(--white);text-align:center;padding-top:50px}
.why .section-title{color:var(--white)}
.why-art{position:absolute;left:0;top:150px}
.why-item{position:absolute;width:290px;font-size:13px;line-height:1.5;color:#d3d9ec}
.why-item b{color:var(--white);font-weight:700}
.why-item.left{text-align:right}
.why-item.right{text-align:left}

/* faq */
.faq{height:640px;padding-top:44px;text-align:center}
.faq-body{display:flex;gap:40px;padding:0 100px;text-align:left}
.faq-list{width:520px}
.q{border:1px solid var(--line);padding:12px 16px;font-size:14px;font-weight:600;color:var(--navy);display:flex;justify-content:space-between;margin-bottom:6px}
.q.open{border-bottom:0;margin-bottom:0}
.a{border:1px solid var(--line);border-top:0;padding:0 16px 14px;font-size:12px;color:var(--muted);line-height:1.5;margin-bottom:6px}
.faq-photo{flex:1;height:420px;background:linear-gradient(180deg,#e9d9b8 0%,#8d7358 55%,#3a3230 100%)}

/* footer */
.site-footer{height:312px;background:linear-gradient(180deg,#16275e,#0c1840);color:var(--white);position:relative}
.footer-brand{position:absolute;top:22px;left:0;right:0;text-align:center;font-family:"Oswald",sans-serif;font-size:34px;font-weight:600;text-transform:uppercase;letter-spacing:1px}
.footer-cols{position:absolute;top:100px;left:70px;right:60px;display:flex;gap:40px}
.footer-cols h5{font-family:"Oswald",sans-serif;font-size:16px;margin-bottom:12px;letter-spacing:.5px}
.footer-cols p,.footer-cols li{font-size:12px;color:#c9d0e6;line-height:1.6;list-style:none}
.badge{width:150px;height:32px;background:#d8dbe3;border-radius:3px;margin-bottom:8px}
.footer-call{margin-left:auto;background:var(--red);padding:18px 22px;height:110px;display:flex;gap:14px;align-items:center}
.copyright{position:absolute;bottom:0;left:0;right:0;height:36px;background:var(--navy-deep);font-size:11px;color:#aab3cf;display:flex;align-items:center;justify-content:center;letter-spacing:.5px}
</style>
</head>
<body>

<header class="site-header">
  <div class="brand"><span class="dot"></span>Hulls for Heroes</div>
  <div class="call">
    <div class="ring"><svg width="30" height="30" viewBox="0 0 24 24"><path fill="#fff" d="M6.6 10.8a15 15 0 0 0 6.6 6.6l2.2-2.2c.3-.3.7-.4 1-.2 1.1.4 2.3.6 3.6.6.6 0 1 .4 1 1V20c0 .6-.4 1-1 1A17 17 0 0 1 3 4c0-.6.4-1 1-1h3.5c.6 0 1 .4 1 1 0 1.3.2 2.5.6 3.6.1.3 0 .7-.2 1z"/></svg></div>
    <div><small>CALL TODAY TO DONATE</small><strong>1-800-555-0142</strong><em>Live Operators Available 7 Days A Week</em></div>
  </div>
</header>

<nav class="nav">
  <a>HOW TO DONATE</a><a>WHY DONATE</a><a>FAQ</a><a>ABOUT</a>
  <div class="tab">DONATE YOUR BOATS ONLINE</div>
</nav>

<section class="hero">
  <div class="hero-photo" role="img" aria-label="Soldier in uniform holding a small American flag beside a white boat at a marina"></div>
  <form class="donate-form">
    <h3>Full Tax Deduction - Running or Not</h3>
    <div class="row"><div class="field">First Name</div><div class="field">Last Name</div></div>
    <div class="row"><div class="field">Daytime Phone</div><div class="field">Email</div></div>
    <div class="row"><div class="field">Address</div></div>
    <div class="row"><div class="field">Pickup City</div></div>
    <div class="row"><div class="field">Pickup State ▾</div><div class="field">Zip Code</div></div>
    <div class="row"><div class="field">Boat Year ▾</div><div class="field">Running? ▾</div></div>
    <div class="row"><div class="field">Boat Make &amp; Model</div></div>
    <button class="btn" type="button">DONATE NOW</button>
  </form>
</section>

<section class="banner">
  <div class="banner-text head">
    <div class="l1">Donate your boats to</div>
    <div class="l2">Veterans</div>
    <div class="l3">Make a difference</div>
  </div>
  <div class="perks">
    <div class="perk"><div class="ic"><svg width="34" height="34" viewBox="0 0 24 24"><path d="M4 12l5 5L20 6" stroke="#fff" stroke-width="3" fill="none"/></svg></div><p>Tax deduction for your boat</p></div>
    <div class="perk"><div class="ic"><svg width="38" height="30" viewBox="0 0 32 24"><path d="M2 14h28l-5 7H7z M15 2v11 M15 3l8 9h-8" stroke="#fff" stroke-width="2" fill="none"/></svg></div><p>Free pickup, running or not</p></div>
    <div class="perk"><div class="ic"><svg width="34" height="34" viewBox="0 0 24 24"><circle cx="12" cy="12" r="9" stroke="#fff" stroke-width="2" fill="none"/><path d="M12 6v6l4 3" stroke="#fff" stroke-width="2" fill="none"/></svg></div><p>We pick up in 24 to 48 hours</p></div>
    <div class="perk"><div class="ic"><svg width="34" height="34" viewBox="0 0 24 24"><rect x="4" y="3" width="16" height="18" stroke="#fff" stroke-width="2" fill="none"/><path d="M8 8h8M8 12h8M8 16h5" stroke="#fff" stroke-width="2"/></svg></div><p>We take care of all paperwork</p></div>
  </div>
</section>

<section class="how">
  <h2 class="section-title">How to <span>Donate</span></h2>
  <div class="rule"></div>
  <div class="steps">
    <div class="step">
      <svg class="ic" width="56" height="48" viewBox="0 0 56 48"><rect x="4" y="4" width="40" height="40" fill="none" stroke="#1f3f96" stroke-width="3"/><path d="M12 16h24M12 24h24M12 32h16" stroke="#c8202b" stroke-width="3"/></svg>
      <div><h4>CALL US AT 1-800-555-0142 OR FILL OUT THE ONLINE FORM</h4><p>Donating your boat is easy and donation is accepted nationwide.</p></div>
    </div>
    <div class="step">
      <svg class="ic" width="56" height="48" viewBox="0 0 56 48"><path d="M4 30h48l-8 10H12z" fill="#c8202b"/><path d="M26 6v22M26 8l14 18H26" stroke="#1f3f96" stroke-width="3" fill="none"/></svg>
      <div><h4>WE PICK UP THE BOAT</h4><p>Your boat is accepted and we will arrange to pick up your boat when it is most convenient for you.</p></div>
    </div>
    <div class="step">
      <svg class="ic" width="56" height="48" viewBox="0 0 56 48"><rect x="10" y="2" width="30" height="40" fill="none" stroke="#1f3f96" stroke-width="3"/><text x="25" y="30" font-family="Oswald" font-size="18" fill="#c8202b" text-anchor="middle">$</text></svg>
      <div><h4>TAX WRITE-OFF</h4><p>Once the boat donation is complete, you will receive your tax-deductible boat donation receipt.</p></div>
    </div>
  </div>
</section>

<section class="why">
  <h2 class="section-title">Why Donate Your Boats to Us</h2>
  <div class="rule"></div>
  <svg class="why-art" width="1200" height="540" viewBox="0 0 1200 540">
    <circle cx="600" cy="260" r="210" fill="none" stroke="#c8202b" stroke-width="3"/>
    <circle cx="600" cy="260" r="190" fill="#0c1840" stroke="#3b57a8" stroke-width="2"/>
    <g fill="#c8202b" stroke="#fff" stroke-width="3">
      <circle cx="420" cy="140" r="32"/><circle cx="392" cy="260" r="32"/><circle cx="420" cy="380" r="32"/>
      <circle cx="780" cy="140" r="32"/><circle cx="808" cy="260" r="32"/><circle cx="780" cy="380" r="32"/>
    </g>
    <g stroke="#fff" stroke-width="3" fill="none">
      <path d="M408 148h24M414 136h12"/><path d="M380 260l8 8 16-16"/><path d="M408 372h24v16h-24z"/>
      <path d="M772 132h16v16h-16z"/><path d="M796 254h24M796 266h24"/><path d="M768 380l8 8 16-16"/>
    </g>
  </svg>
  <div class="why-art" style="left:460px;top:340px;width:280px;height:140px;border-radius:8px;background:linear-gradient(180deg,#2d4a9e,#b9c4df)" role="img" aria-label="White motor boat with red and blue stripes on open water"></div>
  <div class="why-item left" style="left:70px;top:270px"><b>Free Local Towing</b> - We will pick up your boat donation, running or not, at no cost to you anywhere nearby.</div>
  <div class="why-item left" style="left:60px;top:400px"><b>Quick Tax Deduction</b> - We make sure you get the highest tax write-off allowed for your donated boat.</div>
  <div class="why-item left" style="left:70px;top:520px"><b>No Paperwork Hassle</b> - We take care of the title transfer, DMV forms and all the details.</div>
  <div class="why-item right" style="left:840px;top:270px"><b>IRS 501(c)3 Approved</b> - Give with trust through our fully approved nonprofit.</div>
  <div class="why-item right" style="left:850px;top:400px"><b>Schedule a Free Pickup</b> - Pick a time that fits your week and we handle the rest.</div>
  <div class="why-item right" style="left:840px;top:520px"><b>Boat donations help fund programs</b> - Your gift supports veterans and their families.</div>
</section>

<section class="faq">
  <h2 class="section-title">Frequently Asked <span>Questions</span></h2>
  <div class="rule"></div>
  <div class="faq-body">
    <div class="faq-list">
      <div class="q">What types of boats can be donated? <span>▾</span></div>
      <div class="q open">What paperwork do I need to donate my boat? <span>▴</span></div>
      <div class="a">All you need is a title, first of all then we will request some general information from you at the time of donation such as the year, make and model of the boat, as well as its general mechanical condition. We accept all boats, running or not running.</div>
      <div class="q">Is my donated boat tax-deductible? <span>▾</span></div>
      <div class="q">What if the boat is not registered in my name? <span>▾</span></div>
      <div class="q">How much will I receive as a tax deduction for my boat? <span>▾</span></div>
      <div class="q">When will I receive my tax receipt? <span>▾</span></div>
      <div class="q">How do I schedule a pick up? <span>▾</span></div>
    </div>
    <div class="faq-photo" role="img" aria-label="Silhouettes of soldiers raising a large American flag against a sunset sky"></div>
  </div>
</section>

<footer class="site-footer">
  <div class="footer-brand">Hulls for Heroes</div>
  <div class="footer-cols">
    <div style="width:260px"><h5>ABOUT HULLS FOR HEROES</h5><p>We turn donated boats into support for veterans across the country. Every gift helps fund care, housing and job programs for those who served our nation.</p></div>
    <div><h5>NAVIGATION</h5><ul><li>How to Donate</li><li>Why Donate</li><li>FAQ</li><li>About</li></ul></div>
    <div><h5>SAFE &amp; SECURE</h5><div class="badge"></div><div class="badge"></div></div>
    <div class="footer-call">
      <svg width="44" height="44" viewBox="0 0 24 24"><circle cx="12" cy="12" r="11" fill="none" stroke="#fff" stroke-width="1.5"/><path fill="#fff" d="M8.4 10.9a9 9 0 0 0 4 4l1.3-1.3c.2-.2.4-.2.6-.1.7.2 1.4.4 2.2.4.3 0 .6.2.6.6v2c0 .3-.3.6-.6.6A10 10 0 0 1 6.4 7c0-.3.3-.6.6-.6h2c.4 0 .6.3.6.6 0 .8.1 1.5.4 2.2 0 .2 0 .4-.2.6z"/></svg>
      <div><div class="head" style="font-size:15px">CALL TODAY TO DONATE</div><div class="head" style="font-size:32px;line-height:1">1-800-555-0142</div><div style="font-size:11px">Live Operators Available 7 Days A Week</div></div>
    </div>
  </div>
  <div class="copyright">COPYRIGHT © 2017 HULLS FOR HEROES. PRIVACY POLICY | TERMS &amp; CONDITIONS. ALL RIGHTS RESERVED.</div>
</footer>

</body>
</html>
```